Brightfen Business Card Redesign & Logo Update

We need to update our business cards to something more modern and fresh. Brightfen can provide the current color schemes and old design examples, but welcome creativity in helping us with this redesign. PLEASE NOTE that we no longer utilize the "tree" and/or "leaf" imagery in our branding. If able would apprecaite an update on the quality of our "words only" logo in Ai. / PNG formats too.

Target Market(s)

Investors, landowners, corporate partners, contractors

Industry/Entity Type

Environmental Restoration & Conservation

Contact Information for Business Card

Logo, persons name, title, mailing address, phone and email, website url

Font styles to use
Other font styles liked:
• Merriweather

Requirements
Nice to have
• Logo, persons name, title, mailing address, phone and email, website url, but open to ideams
Should not have
• No all back backgrounds

```html
<!DOCTYPE html>
<html lang="en">
<head>
<meta charset="utf-8">
<title>Brightfen Business Card</title>
<link rel="stylesheet" href="https://fonts.googleapis.com/css2?family=Oswald:wght@600&family=Open+Sans:wght@400;700&display=swap">
<style>
  :root {
    --bg: #e7e8ea;
    --card-dark: #221f24;
    --orange: #ec7d22;
    --green: #18813a;
    --white: #ffffff;
    --text-soft: #e9e9e9;
  }
  * { margin: 0; padding: 0; box-sizing: border-box; }
  html, body { width: 1200px; height: 780px; overflow: hidden; }
  body { background: var(--bg); position: relative; font-family: "Open Sans", sans-serif; }

  .card {
    position: absolute;
    top: 241px;
    width: 520px;
    height: 297px;
    overflow: hidden;
    box-shadow: 0 10px 26px rgba(0,0,0,.22);
  }
  .card-front { left: 50px; background: var(--card-dark); }
  .card-back { left: 630px; background: var(--orange); }

  .front-swoosh { position: absolute; inset: 0; width: 100%; height: 100%; }

  .wordmark, .tagline {
    position: absolute;
    font-family: "Oswald", sans-serif;
    font-weight: 600;
    text-transform: uppercase;
    line-height: 1;
    white-space: nowrap;
  }
  .tagline { color: var(--white); }

  .card-front .wordmark { left: 190px; top: 30px; font-size: 58px; color: var(--orange); }
  .card-front .tagline { left: 191px; top: 104px; font-size: 14px; letter-spacing: .3px; }

  .person { position: absolute; left: 70px; top: 134px; }
  .person-name { font-weight: 700; font-size: 21px; line-height: 1.1; white-space: nowrap; }
  .person-first { color: var(--orange); }
  .person-last { color: var(--green); }
  .person-title { color: var(--text-soft); font-size: 13px; margin-top: 3px; }

  .divider {
    position: absolute;
    left: 262px; top: 176px;
    width: 1.5px; height: 76px;
    background: var(--white);
  }

  .contact-list {
    position: absolute;
    left: 280px; top: 174px;
    list-style: none;
  }
  .contact-list li {
    display: flex; align-items: center; gap: 9px;
    color: var(--text-soft);
    font-size: 14px;
    height: 20px;
    white-space: nowrap;
  }
  .contact-list svg { width: 13px; height: 13px; fill: var(--orange); flex: none; }

  .card-back .wordmark {
    left: 0; right: 0; top: 62px;
    text-align: center;
    font-size: 104px;
    color: var(--white);
  }
  .card-back .tagline {
    left: 0; right: 0; top: 190px;
    text-align: center;
    font-size: 26px;
    letter-spacing: .8px;
  }
</style>
</head>
<body>

<section class="card card-front" aria-label="Business card front">
  <svg class="front-swoosh" viewBox="0 0 520 297" preserveAspectRatio="none" aria-hidden="true">
    <path d="M0,205 C25,300 330,300 520,262 L520,297 L0,297 Z" fill="var(--orange)"/>
    <path d="M16,200 C44,284 300,288 478,260" fill="none" stroke="var(--green)" stroke-width="3" stroke-linecap="round"/>
  </svg>

  <p class="wordmark">Brightfen</p>
  <p class="tagline">Environmental Credit Company</p>

  <div class="person">
    <p class="person-name"><span class="person-first">Marta</span> <span class="person-last">Kovalik</span></p>
    <p class="person-title">Managing Director</p>
  </div>

  <span class="divider"></span>

  <ul class="contact-list">
    <li>
      <svg viewBox="0 0 24 24"><path d="M6.6 10.8a15.2 15.2 0 0 0 6.6 6.6l2.2-2.2a1 1 0 0 1 1-.25 11.4 11.4 0 0 0 3.6.57 1 1 0 0 1 1 1V20a1 1 0 0 1-1 1A17 17 0 0 1 3 4a1 1 0 0 1 1-1h3.5a1 1 0 0 1 1 1c0 1.25.2 2.45.57 3.57a1 1 0 0 1-.25 1z"/></svg>
      (555) 201-4837
    </li>
    <li>
      <svg viewBox="0 0 24 24"><path d="M4 6h16a1 1 0 0 1 1 1v3H3V7a1 1 0 0 1 1-1zm-1 6h18v6a1 1 0 0 1-1 1H4a1 1 0 0 1-1-1zm5 2v2h8v-2z"/></svg>
      (555) 201-4837
    </li>
    <li>
      <svg viewBox="0 0 24 24"><path d="M3 5h18a1 1 0 0 1 1 1v12a1 1 0 0 1-1 1H3a1 1 0 0 1-1-1V6a1 1 0 0 1 1-1zm9 7.5L4 7.5V9l8 5 8-5V7.5z"/></svg>
      info@brightfen-mail.com
    </li>
    <li>
      <svg viewBox="0 0 24 24"><path d="M12 2a10 10 0 1 0 0 20 10 10 0 0 0 0-20zm6.9 6h-3a15.7 15.7 0 0 0-1.4-3.6A8 8 0 0 1 18.9 8zM12 4c.8 1.2 1.5 2.5 1.9 4h-3.8c.4-1.5 1.1-2.8 1.9-4zM4.3 14a8 8 0 0 1 0-4h3.4a16 16 0 0 0 0 4zm.8 2h3a15.7 15.7 0 0 0 1.4 3.6A8 8 0 0 1 5.1 16zm3-8h-3a8 8 0 0 1 4.4-3.6A15.7 15.7 0 0 0 8.1 8zM12 20c-.8-1.2-1.5-2.5-1.9-4h3.8c-.4 1.5-1.1 2.8-1.9 4zm2.3-6H9.7a14.5 14.5 0 0 1 0-4h4.6a14.5 14.5 0 0 1 0 4zm.2 5.6a15.7 15.7 0 0 0 1.4-3.6h3a8 8 0 0 1-4.4 3.6zm1.8-5.6a16 16 0 0 0 0-4h3.4a8 8 0 0 1 0 4z"/></svg>
      www.brightfen-site.com
    </li>
  </ul>
</section>

<section class="card card-back" aria-label="Business card back">
  <p class="wordmark">Brightfen</p>
  <p class="tagline">Environmental Credit Company</p>
</section>

</body>
</html>
```